Kestrada LLC, needs a web page no more than 5 pages (for now)

Kestrada is a general contractor. Our services include general contracting, design-build construction, disaster recovery and environmental remediation. Our main clients are PMX, TQ, State and Local Gov't Agencies, Hospitals and Schools. Kestrada is also a SDVOSB.

```html
<!DOCTYPE html>
<html lang="en">
<head>
<meta charset="utf-8">
<title>Kestrada LLC — General Contracting</title>
<link href="https://fonts.googleapis.com/css2?family=Poppins:ital,wght@0,400;0,500;0,600;0,700;1,400&display=swap" rel="stylesheet">
<style>
:root{
  --gold:#bf9b44;
  --gold-dark:#a88630;
  --dark:#2b2b2b;
  --black:#0e0e0e;
  --ink:#222;
  --muted:#555;
  --light:#f7f7f7;
  --white:#fff;
}
*{box-sizing:border-box;margin:0;padding:0}
html,body{width:1200px;height:4298px;overflow:hidden}
body{font-family:"Poppins",sans-serif;color:var(--ink);background:var(--white);position:relative}
.abs{position:absolute}
a{color:inherit;text-decoration:none}

/* top bar + nav */
.topbar{top:0;left:0;width:1200px;height:40px;background:#1c1c1c;color:#fff;font-size:13px;display:flex;justify-content:flex-end;align-items:center;gap:30px;padding-right:113px}
.topbar span{display:flex;align-items:center;gap:10px}
.nav{top:40px;left:0;width:1200px;height:55px;background:var(--black);display:flex;align-items:center;padding:0 113px}
.brand{display:flex;align-items:center;gap:8px;color:var(--gold);font-weight:600;font-size:16px}
.brand i{width:14px;height:14px;border-radius:50%;background:var(--gold);display:block}
.menu{display:flex;gap:52px;margin-left:auto;margin-right:30px;color:#fff;font-size:14px}
.menu .on{color:var(--gold)}
.btn{background:var(--gold);color:#fff;font-weight:600;font-size:12px;text-transform:uppercase;display:flex;align-items:center;justify-content:center;border-radius:4px}
.nav .btn{width:142px;height:35px}

/* hero */
.hero{top:95px;left:0;width:1200px;height:660px;background:linear-gradient(100deg,#1d2a33 0%,#3b4a55 45%,#5b5a3f 75%,#2f3326 100%)}
.hero::after{content:"";position:absolute;inset:0;background:linear-gradient(90deg,rgba(0,0,0,.45),rgba(0,0,0,.1))}
.hero-title{top:260px;left:110px;font-size:52px;font-weight:600;line-height:60px;color:#fff;z-index:2}
.hero-sub{top:390px;left:113px;font-size:15px;line-height:18px;color:#fff;z-index:2}
.hero .btn{}
.hero-btn{top:456px;left:113px;width:224px;height:55px;font-size:14px;z-index:2}
.hero-cut{top:590px;left:0;z-index:3}

/* section headings */
h2{font-size:30px;font-weight:600;color:var(--ink)}
.center{text-align:center;width:1200px;left:0}

/* clients */
.clients-title{top:698px}
.clients-text{top:757px;font-size:14px;line-height:22px;color:var(--muted)}
.client{top:832px;width:160px;text-align:center;font-size:15px;font-weight:500;line-height:18px}
.client .seal{width:130px;height:130px;border-radius:50%;margin:0 auto 22px}

/* projects */
.projects{top:1062px;left:0;width:1200px;height:686px;background:var(--light)}
.sub{font-size:13px;color:#444}
.proj{top:1232px;width:335px;height:334px}
.proj-label{top:1588px;font-size:15px;font-weight:500}
.track{top:1667px;left:112px;width:681px;height:5px;background:#ddd;border-radius:3px}
.track i{display:block;width:182px;height:5px;background:var(--gold);border-radius:3px}

/* services */
.svc{top:1924px;width:236px;height:299px}
.svc-cap{position:absolute;left:0;bottom:0;width:100%;height:57px;background:var(--gold);color:#fff;text-align:center;padding-top:11px}
.svc-cap b{display:block;font-size:15px;font-weight:600}
.svc-cap small{font-size:10px}

/* testimonial + about */
.quote-box{top:2308px;left:112px;width:975px;height:416px;background:var(--gold);z-index:2;box-shadow:0 8px 30px rgba(0,0,0,.2)}
.quote-text{top:120px;left:135px;width:780px;font-size:25px;font-style:italic;line-height:28px;color:#fff}
.quote-name{top:257px;left:135px;color:#fff;font-weight:600;font-size:16px;display:flex;gap:22px;align-items:center}
.quote-role{top:284px;left:135px;color:#fff;font-size:15px}
.about-title{top:2932px;left:112px;color:#fff}
.about-p{left:112px;width:455px;font-size:12.5px;line-height:20px;color:#fff}
.outline-btn{top:3311px;left:112px;width:134px;height:34px;background:#fff;color:var(--ink);font-size:11px;display:flex;align-items:center;justify-content:center;border-radius:3px}

/* contact */
.contact{top:3522px;left:0;width:1200px;height:420px;background:var(--gold)}
.eyebrow{top:3594px;left:112px;color:#fff;font-size:14px}
.contact-title{top:3612px;left:110px;color:#fff;font-size:50px;font-weight:600}
.field{width:194px;border-bottom:1px solid rgba(255,255,255,.35);color:#fff;font-size:12px;padding-bottom:12px}
.send{top:3770px;left:826px;width:261px;height:40px;background:#1d1d1d;color:#fff;font-weight:600;font-size:14px;display:flex;align-items:center;justify-content:center;border-radius:4px}

/* footer */
.footer{top:3939px;left:0;width:1200px;height:359px;background:var(--dark)}
.flogo{top:4080px;left:112px;color:var(--gold);font-size:34px;font-weight:500;display:flex;align-items:center;gap:12px}
.flogo i{width:30px;height:30px;border-radius:50%;border:3px solid var(--gold);display:block}
.fcol{top:4027px;color:#fff;font-size:13px}
.fcol h4{font-size:14px;font-weight:600;margin-bottom:14px}
.fcol li{list-style:none;line-height:34px;font-size:13px}
.fcontact li{display:flex;align-items:center;gap:14px}
.fdivider{top:4138px;left:845px;width:242px;height:1px;background:#888}
.socials{top:4160px;left:850px;display:flex;gap:26px}
.socials i{width:16px;height:16px;border-radius:50%;border:2px solid #fff;display:block}
.copy{top:4262px;font-size:11px;color:#fff}
</style>
</head>
<body>

<div class="abs topbar">
  <span><svg width="16" height="16" viewBox="0 0 24 24"><path fill="#fff" d="M6.6 10.8a15 15 0 0 0 6.6 6.6l2.2-2.2c.3-.3.7-.4 1-.2 1.1.4 2.3.6 3.6.6.6 0 1 .4 1 1V20c0 .6-.4 1-1 1A17 17 0 0 1 3 4c0-.6.4-1 1-1h3.5c.6 0 1 .4 1 1 0 1.3.2 2.5.6 3.6.1.3 0 .7-.2 1z"/></svg>503-555-0148</span>
  <span><svg width="18" height="13" viewBox="0 0 18 13"><rect x="0.5" y="0.5" width="17" height="12" fill="none" stroke="#fff"/><path d="M1 1l8 6 8-6" fill="none" stroke="#fff"/></svg>hello@kestrada-build.com</span>
</div>

<header class="abs nav">
  <div class="brand"><i></i>Kestrada</div>
  <nav class="menu"><a class="on">Home</a><a>About</a><a>Services</a><a>Our Clients</a><a>Projects</a><a>Contact Us</a></nav>
  <a class="btn">Get In Touch</a>
</header>

<section class="abs hero" role="img" aria-label="Photo of contractors and service members reviewing plans on a laptop"></section>
<h1 class="abs hero-title">Building with Precision.<br>Serving with Kestrada.</h1>
<p class="abs hero-sub">General Contracting • Design-Build • Disaster Recovery<br>Environmental Remediation.</p>
<a class="abs btn hero-btn">Work With Us</a>
<svg class="abs hero-cut" width="1200" height="170" viewBox="0 0 1200 170">
  <polygon points="0,153 600,14 1200,153 1200,170 0,170" fill="#bf9b44"/>
  <polygon points="0,164 600,26 1200,164 1200,170 0,170" fill="#fff"/>
  <circle cx="600" cy="7" r="28" fill="#fff"/>
  <path d="M586 0 L600 16 L614 0" fill="none" stroke="#333" stroke-width="2.5"/>
</svg>

<h2 class="abs center clients-title">Our Clients</h2>
<p class="abs center clients-text">Every pleasure is to be welcomed and every pain avoided. But in certain circumstances and<br>owing to the claims of duty obligations of business it will frequently occur that.</p>
<div class="abs client" style="left:99px"><div class="seal" style="background:#2b4f8a"></div>PMX</div>
<div class="abs client" style="left:302px"><div class="seal" style="background:#1e2f57"></div>TQ</div>
<div class="abs client" style="left:508px"><div class="seal" style="background:#5a6f3a"></div>State and Local<br>Gov't Agencies</div>
<div class="abs client" style="left:710px"><div class="seal" style="background:var(--gold)"></div>Hospitals</div>
<div class="abs client" style="left:914px"><div class="seal" style="background:#1d3d7a;border-radius:8px"></div>Schools</div>

<section class="abs projects"></section>
<h2 class="abs" style="top:1122px;left:112px">Our Projects</h2>
<p class="abs sub" style="top:1170px;left:112px">Standard Mortgage Originates Residential Home loans in Florida.</p>
<a class="abs btn" style="top:1155px;left:953px;width:134px;height:35px">View More</a>
<div class="abs proj" style="left:112px;background:linear-gradient(160deg,#45525c,#2a3036)" role="img" aria-label="Photo of engineers reviewing a laptop in a facility"></div>
<div class="abs proj" style="left:464px;background:linear-gradient(180deg,#c9ccd0,#7a6d5e)" role="img" aria-label="Photo of a hospital building under construction with a crane"></div>
<div class="abs proj" style="left:816px;background:linear-gradient(180deg,#cfd6de 0%,#aab3bc 55%,#5c4f40 100%)" role="img" aria-label="Photo of a large water pipe and excavator on site"></div>
<div class="abs proj" style="left:1167px;width:40px;background:linear-gradient(180deg,#dfe6ee,#b7c3cf)" role="img" aria-label="Photo of a further project"></div>
<div class="abs proj-label" style="left:112px">Military / PMX Renovations</div>
<div class="abs proj-label" style="left:464px">Hospital Renovations</div>
<div class="abs proj-label" style="left:816px">Waterlines Construction</div>
<div class="abs proj-label" style="left:1167px;color:#999;font-weight:400">12 Su</div>
<div class="abs track"><i></i></div>

<h2 class="abs" style="top:1809px;left:112px">Our Services</h2>
<p class="abs sub" style="top:1856px;left:112px">Lorem Ipsum is simply dummy text of the printing and typesetting industry.</p>
<a class="abs btn" style="top:1833px;left:936px;width:151px;height:35px;text-transform:none;font-weight:500;font-size:13px">View All Services</a>
<div class="abs svc" style="left:112px;background:linear-gradient(170deg,#b9b3a6,#6f6a5e)" role="img" aria-label="Photo of construction workers in hard hats"><div class="svc-cap"><b>General Contracting</b><small>Learn More</small></div></div>
<div class="abs svc" style="left:357px;background:linear-gradient(170deg,#e9e6df,#9b9588)" role="img" aria-label="Photo of architects reviewing drawings"><div class="svc-cap"><b>Design-Build Construction</b><small>Learn More</small></div></div>
<div class="abs svc" style="left:603px;background:linear-gradient(170deg,#c4c7c9,#4a4c47)" role="img" aria-label="Photo of a worker near heavy machinery"><div class="svc-cap"><b>Disaster Recovery</b><small>Learn More</small></div></div>
<div class="abs svc" style="left:851px;background:linear-gradient(170deg,#9fb6cc,#5f6e63)" role="img" aria-label="Photo of a worker at an environmental site"><div class="svc-cap"><b>Environmental Remediation</b><small>Learn More</small></div></div>

<svg class="abs" style="top:2390px;left:0" width="1200" height="1140" viewBox="0 0 1200 1140">
  <polygon points="0,0 600,95 1200,0 1200,18 600,113 0,18" fill="#8a8a8a"/>
  <polygon points="0,18 600,113 1200,18 1200,1140 0,1140" fill="#2b2b2b"/>
  <polygon points="1200,205 688,815 1102,1132 1200,1132" fill="#8c7437"/>
  <polygon points="851,426 688,606 851,739" fill="#fff"/>
</svg>

<div class="abs quote-box">
  <svg class="abs" style="top:112px;left:60px" width="50" height="50" viewBox="0 0 50 50"><circle cx="25" cy="25" r="23" fill="none" stroke="#fff" stroke-width="2.5"/><path d="M15 31v-6c0-4 2-7 6-8M27 31v-6c0-4 2-7 6-8" fill="none" stroke="#fff" stroke-width="4" stroke-linecap="round"/></svg>
  <p class="abs quote-text">“I should be incapable of drawing a single stroke at the present moment; and yet I feel that I never was a greater artist than now. The lovely valley teems with vapor around me, &amp; the meridian sun strikes.</p>
  <div class="abs quote-name">Marcus Delaney
    <svg width="110" height="20" viewBox="0 0 110 20"><g fill="#fff"><path id="s" d="M10 0l2.9 6.5 7.1.7-5.4 4.7 1.6 7L10 15.3 3.8 18.9l1.6-7L0 7.2l7.1-.7z"/><use href="#s" x="22"/><use href="#s" x="44"/><use href="#s" x="66"/><use href="#s" x="88"/></g></svg>
  </div>
  <div class="abs quote-role">CEO</div>
</div>

<h2 class="abs about-title">About Us</h2>
<p class="abs about-p" style="top:2996px">Contrary to popular belief, Lorem Ipsum is not simply random text. It has roots in a piece of classical Latin literature from 45 BC, making it over 2000 years old. Daniel Whitcombe, a Latin professor at Ashford College in Vermont, looked up one of the more obscure Latin words, consectetur, from a Lorem Ipsum passage, and going through the cites of the word in classical literature, discovered the undoubtable source.</p>
<p class="abs about-p" style="top:3148px">Contrary to popular belief, Lorem Ipsum is not simply random text. It has roots in a piece of classical Latin literature from 45 BC, making it over 2000 years old. Daniel Whitcombe, a Latin professor at Ashford College in Vermont, looked up one of the more obscure Latin words, consectetur, from a Lorem Ipsum passage, and going through the cites of the word in classical literature, discovered the undoubtable source.</p>
<a class="abs outline-btn">LEARN MORE</a>

<section class="abs contact"></section>
<p class="abs eyebrow">Contact</p>
<h2 class="abs contact-title">Get In Touch</h2>
<div class="abs field" style="top:3712px;left:112px">First Name*</div>
<div class="abs field" style="top:3712px;left:352px">Service*</div>
<div class="abs field" style="top:3712px;left:586px;border:none">Message*</div>
<div class="abs field" style="top:3781px;left:112px">Phone Number*</div>
<div class="abs field" style="top:3781px;left:352px">Email Address*</div>
<a class="abs send">SEND MESSAGE</a>

<footer class="abs footer"></footer>
<svg class="abs" style="top:3938px;left:0" width="1200" height="62" viewBox="0 0 1200 62"><polygon points="0,0 1200,0 1200,2 600,59 0,2" fill="#bf9b44"/></svg>
<div class="abs flogo"><i></i>Kestrada</div>
<div class="abs fcol" style="left:422px"><h4>Quick Links</h4><ul><li>About</li><li>Services</li><li>Projects</li><li>Clients</li><li>Contact Us</li></ul></div>
<div class="abs fcol" style="left:601px"><h4>Services</h4><ul><li>General Contracting</li><li>Design-Build Construction</li><li>Disaster Recovery</li><li>Environmental Remediation</li></ul></div>
<div class="abs fcol fcontact" style="left:845px"><h4>Contact Us</h4><ul>
  <li><svg width="14" height="14" viewBox="0 0 24 24"><path fill="#fff" d="M6.6 10.8a15 15 0 0 0 6.6 6.6l2.2-2.2c.3-.3.7-.4 1-.2 1.1.4 2.3.6 3.6.6.6 0 1 .4 1 1V20c0 .6-.4 1-1 1A17 17 0 0 1 3 4c0-.6.4-1 1-1h3.5c.6 0 1 .4 1 1 0 1.3.2 2.5.6 3.6.1.3 0 .7-.2 1z"/></svg>1-888-555-0199</li>
  <li><svg width="15" height="11" viewBox="0 0 18 13"><rect x="0.5" y="0.5" width="17" height="12" fill="none" stroke="#fff"/><path d="M1 1l8 6 8-6" fill="none" stroke="#fff"/></svg>hello@kestrada-build.com</li>
</ul></div>
<div class="abs fdivider"></div>
<div class="abs socials"><i></i><i></i><i></i></div>
<p class="abs center copy">Copyright © Kestrada 2025 &nbsp;|&nbsp; All Rights Reserved</p>

</body>
</html>
```